Professional Package for CPA Firm

We would like a stationery design for our new CPA Firm based in Atlanta, GA called 'Vale 8'. We work with investors to help grow investments, tax free. We would like the design to have a professional/minimal look with a 'wow' factor. We need 9.5″ x 4.125″, 9x12, and 10x13 mailing envelopes, business cards, and a letterhead. We have a logo that is already complete. For the letterhead, we would like to have space to put credentials at the bottom of the page

Industry/Entity Type

CPA, Accounting

```html
<!DOCTYPE html>
<html lang="en">
<head>
<meta charset="utf-8">
<title>Vale 8 – Business Cards</title>
<link rel="stylesheet" href="https://fonts.googleapis.com/css2?family=Open+Sans:wght@400;600;700&display=swap">
<style>
  :root {
    --navy: #0b2a47;
    --navy-deep: #082238;
    --teal: #1fa9b8;
    --red: #ee4450;
    --white: #ffffff;
    --paper: #f3f3f3;
    --backdrop: #d9d9db;
    --bright-blue: #1e9ee6;
    --rule: #1a6e86;
  }
  * { margin: 0; padding: 0; box-sizing: border-box; }
  html, body { width: 1200px; height: 800px; overflow: hidden; }
  body {
    background: var(--backdrop);
    font-family: "Open Sans", Arial, sans-serif;
    position: relative;
  }
  .card {
    position: absolute;
    top: 246px;
    width: 540px;
    height: 309px;
    border-radius: 22px;
    overflow: hidden;
    background: var(--navy);
  }
  .card--front { left: 40px; }
  .card--back { left: 620px; background: var(--navy-deep); }

  .card__wave { position: absolute; inset: 0; width: 100%; height: 100%; }

  .brand { position: absolute; display: flex; flex-direction: column; align-items: flex-start; }
  .brand__row { display: flex; align-items: center; gap: 10px; }
  .brand__dot { width: 14px; height: 14px; border-radius: 50%; }
  .brand__name { font-weight: 700; letter-spacing: 3px; line-height: 1; }
  .brand__tagline { letter-spacing: 1.5px; margin-top: 6px; }

  .card--front .brand { left: 42px; top: 92px; }
  .card--front .brand__dot { background: var(--red); }
  .card--front .brand__name { color: var(--white); font-size: 40px; }
  .card--front .brand__tagline { color: var(--white); font-size: 11px; }

  .divider {
    position: absolute;
    left: 262px; top: 44px;
    width: 1px; height: 122px;
    background: var(--rule);
  }

  .contact { position: absolute; left: 284px; top: 38px; color: var(--white); }
  .contact__name { color: var(--teal); font-size: 17px; font-weight: 600; letter-spacing: 0.5px; line-height: 1.1; }
  .contact__role { color: var(--red); font-size: 12px; margin-bottom: 10px; }
  .contact__address { font-size: 11.5px; line-height: 1.35; margin-bottom: 10px; }
  .contact__list { list-style: none; font-size: 11.5px; line-height: 1.45; }
  .contact__list li { display: flex; align-items: center; gap: 7px; }
  .contact__icon { width: 10px; height: 10px; flex: none; }

  .website {
    position: absolute;
    left: 372px; top: 244px;
    color: var(--navy);
    font-size: 12px;
    letter-spacing: 2px;
    transform: rotate(9deg);
    transform-origin: left center;
  }
  .website strong { font-weight: 700; }

  .card--back .brand { left: 50%; top: 50%; transform: translate(-50%, -50%); align-items: center; }
  .card--back .brand__dot { background: var(--bright-blue); width: 18px; height: 18px; }
  .card--back .brand__name { color: var(--bright-blue); font-size: 56px; }
  .card--back .brand__tagline { color: var(--bright-blue); font-size: 14px; letter-spacing: 3px; margin-top: 10px; }
</style>
</head>
<body>
  <section class="card card--front" aria-label="Business card front">
    <svg class="card__wave" viewBox="0 0 540 309" preserveAspectRatio="none" aria-hidden="true">
      <path d="M0,258 C150,260 280,248 360,220 C430,196 500,216 540,280 L540,309 L0,309 Z" fill="var(--red)"/>
      <path d="M0,258 C150,261 280,252 360,226 C430,203 500,222 540,285 L540,309 L0,309 Z" fill="var(--teal)"/>
      <path d="M0,272 C150,271 280,260 360,234 C430,212 500,230 540,290 L540,309 L0,309 Z" fill="var(--paper)"/>
    </svg>

    <div class="brand">
      <div class="brand__row">
        <span class="brand__dot"></span>
        <span class="brand__name">VALE 8</span>
      </div>
      <span class="brand__tagline">CPAs and Tax Advisors</span>
    </div>

    <div class="divider"></div>

    <div class="contact">
      <p class="contact__name">DANIEL HART</p>
      <p class="contact__role">President</p>
      <p class="contact__address">1420 Birchwood Court<br>Marietta, Georgia 30062</p>
      <ul class="contact__list">
        <li>
          <svg class="contact__icon" viewBox="0 0 10 10" aria-hidden="true"><path d="M2,0.5 L4,2.8 L3,4 C3.6,5.3 4.7,6.4 6,7 L7.2,6 L9.5,8 L8.3,9.5 C4.5,9.2 0.8,5.5 0.5,1.7 Z" fill="var(--red)"/></svg>
          404-555-0172
        </li>
        <li>
          <svg class="contact__icon" viewBox="0 0 10 10" aria-hidden="true"><rect x="2" y="0.5" width="6" height="9" rx="1" fill="none" stroke="var(--red)" stroke-width="1.2"/></svg>
          404-555-0189
        </li>
        <li>
          <svg class="contact__icon" viewBox="0 0 10 10" aria-hidden="true"><rect x="0.5" y="2" width="9" height="6.5" fill="var(--red)"/><path d="M0.5,2 L5,5.5 L9.5,2" fill="none" stroke="var(--navy)" stroke-width="0.9"/></svg>
          hello@vale8.com
        </li>
      </ul>
    </div>

    <p class="website">WWW.<strong>VALE8</strong>.COM</p>
  </section>

  <section class="card card--back" aria-label="Business card back">
    <div class="brand">
      <div class="brand__row">
        <span class="brand__dot"></span>
        <span class="brand__name">VALE 8</span>
      </div>
      <span class="brand__tagline">CPAs and Tax Advisors</span>
    </div>
  </section>
</body>
</html>
```